Company website for an international IT business

We require a website for our business, Korvel Solutions. The business has two primary areas: Lanterns, which includes two machine learning/deep learning based products and IT consultancy, which is the service we provide to other businesses.

We bridge cutting-edge research to market.

STYLING:
The site can be on single page or multi-page. This is fully open to suggestion. So long as the look and feel are consistent. Currently, we have no strong preference for colors, styles or layouts.
You can find the logo of our website in the attachment “Korvel-logo.png” and “Korvel-logo-landscape.png”.

CONTENT:
You can find the text of the website in “Website-Content.pdf”, which explains the services and products of our business. The format of the text is also open to suggestion - including breaking up the text into visually appealing sections.
We would also like to include suitable images on the website so that it does not appear to be a text-heavy page. We are happy to have placeholder images on stock image sites if needed. We are open to suggestions on placing of images

ATTACHMENT:

Industry/Entity Type

It Company

Coding

Coded - Design and coding required

Number of Pages Required

1 page

Colors

Designer to choose colors to be used in the design.

Requirements
Must have
• A full description of the requirement is in the attachment "Website-Content.pdf"
• The design must have HTML/CSS, and all resources relevant (images, fonts etc)
• We are
Nice to have
• We are open to suggestions on top of the requirement, please reach out and communicate.

```html
<!DOCTYPE html>
<html lang="en">
<head>
<meta charset="utf-8">
<title>Korvel Solutions — IT expertise for your business at any stage</title>
<link rel="stylesheet" href="https://fonts.googleapis.com/css2?family=Montserrat:wght@500;600&family=Roboto:wght@300;400;500&display=swap">
<style>
:root{
  --blue:#0a7cc1;
  --blue-deep:#0768a6;
  --ink:#222222;
  --text:#4a4a4a;
  --muted:#6b6b6b;
  --grey:#e3e3e3;
  --light:#f1f1f1;
  --charcoal:#3a3a3a;
  --black:#111111;
  --white:#ffffff;
}
*{box-sizing:border-box;margin:0;padding:0}
html,body{width:1200px;height:3141px;overflow:hidden}
body{font-family:"Roboto",Arial,sans-serif;color:var(--text);background:var(--white);position:relative}

/* Header + hero */
.hero{position:relative;height:640px;overflow:hidden}
.hero-photo{position:absolute;inset:0;background:linear-gradient(100deg,#1d2326 0%,#3b3f41 35%,#2a2e30 60%,#50565a 100%)}
.hero-shade{position:absolute;inset:0;background:rgba(0,0,0,.25)}
.site-header{position:absolute;top:0;left:0;right:0;height:120px;z-index:3}
.brand{position:absolute;left:120px;top:20px;display:flex;align-items:center;gap:16px}
.brand-dot{width:84px;height:84px;border-radius:50%;background:var(--blue)}
.brand-name{font-family:"Montserrat",Arial,sans-serif;font-weight:600;font-size:26px;letter-spacing:2px;color:var(--white)}
.main-nav{position:absolute;top:50px;right:125px;display:flex;gap:46px}
.main-nav a{font-family:"Roboto",Arial,sans-serif;font-size:16px;font-weight:400;color:var(--white);text-decoration:none;letter-spacing:.5px;padding-bottom:8px}
.main-nav a.active{border-bottom:2px solid var(--white)}
.hero-title{position:absolute;top:262px;left:0;right:0;text-align:center;color:var(--white);font-family:"Montserrat",Arial,sans-serif;font-weight:500;z-index:2}
.hero-title .line1{display:block;font-size:36px;letter-spacing:1px}
.hero-title .line2{display:block;font-size:44px;letter-spacing:1.5px;margin-top:4px}
.hero-cut{position:absolute;left:0;bottom:0;z-index:2}
.slider-dots{position:absolute;top:584px;left:0;right:0;display:flex;justify-content:center;gap:8px;z-index:3}
.slider-dots span{width:14px;height:14px;border-radius:50%;background:var(--white)}
.slider-dots span.current{background:transparent;border:2px solid var(--white)}

/* Section headings */
.section-title{font-family:"Roboto",Arial,sans-serif;font-weight:500;font-size:32px;color:var(--black);text-align:center;letter-spacing:.5px}
.divider{display:flex;align-items:center;justify-content:center;gap:10px;margin-top:14px}
.divider i{display:block;width:130px;height:1px;background:#b5b5b5}
.divider b{display:block;width:34px;height:34px;border-radius:50%;background:var(--blue)}

/* About */
.about{background:var(--grey);height:417px;padding-top:34px;text-align:center}
.about .lead{font-size:17px;line-height:28px;color:var(--text);width:780px;margin:22px auto 0}
.about .body{font-size:12.5px;line-height:27px;color:var(--muted);width:810px;margin:18px auto 0}
.btn-outline{display:inline-block;border:1.5px solid #555;color:var(--ink);font-size:15px;font-weight:500;letter-spacing:.5px;text-decoration:none;text-align:center}
.about .btn-outline{width:168px;height:48px;line-height:45px;margin-top:40px}

/* Lanterns intro */
.lanterns{height:237px;padding-top:48px;text-align:center;background:var(--white)}
.lanterns p{font-size:17px;line-height:28px;color:var(--muted);width:600px;margin:20px auto 0}

/* Product rows */
.product-row{display:flex;height:399px}
.product-row > div{width:50%;height:100%}
.product-copy{padding:75px 0 0 119px}
.product-copy.blue{background:var(--blue);color:var(--white)}
.product-copy.dark{background:var(--charcoal);color:var(--white);padding:64px 0 0 662px;width:100%}
.product-copy h3{font-family:"Roboto",Arial,sans-serif;font-weight:400;font-size:30px;margin-bottom:18px}
.product-copy p{font-size:13px;line-height:23px;width:450px}
.product-copy p + p{margin-top:12px}
.btn-light{display:inline-block;border:1.5px solid var(--white);color:var(--white);font-size:12px;letter-spacing:.5px;text-decoration:none;text-align:center;width:138px;height:35px;line-height:32px;margin-top:20px}
.photo{height:100%}
.photo-office{background:linear-gradient(135deg,#eef1f3 0%,#c9cfd3 40%,#7b7f82 70%,#e7eaec 100%)}
.photo-driver{background:linear-gradient(120deg,#5a5f64 0%,#8a7560 40%,#c59a6c 60%,#3e4145 100%)}
.row-wheel{position:relative}
.row-wheel .photo{position:absolute;left:0;top:0;width:595px}

/* Consultancy */
.consultancy{position:relative;height:461px;background:var(--light);overflow:hidden}
.consultancy .photo-meeting{position:absolute;right:0;top:0;width:700px;height:100%;background:linear-gradient(90deg,rgba(241,241,241,1) 0%,rgba(200,205,210,.9) 30%,#8b8d8f 60%,#4d5257 100%)}
.consultancy-copy{position:absolute;left:130px;top:90px;width:480px}
.consultancy-copy h2{font-family:"Roboto",Arial,sans-serif;font-weight:400;font-size:30px;color:var(--black);margin-bottom:18px}
.consultancy-copy p{font-size:14px;line-height:24px;color:var(--text)}
.consultancy-copy p + p{margin-top:12px}
.consultancy-copy .btn-outline{width:166px;height:47px;line-height:44px;margin-top:26px;font-size:16px}

/* Contact */
.contact{position:relative;height:519px;background:linear-gradient(180deg,#0b87cf 0%,var(--blue) 50%,var(--blue-deep) 100%);color:var(--white)}
.contact .section-title{color:var(--white);font-weight:400;font-size:30px;padding-top:36px}
.contact .divider i{background:rgba(255,255,255,.6)}
.contact .divider b{background:var(--white);width:36px;height:36px}
.contact-form{position:absolute;left:130px;top:157px;width:456px}
.field{display:block;width:100%;height:45px;background:var(--white);border:0;margin-bottom:8px;padding:0 16px;font-family:"Roboto",Arial,sans-serif;font-size:14px;color:#555;line-height:45px}
.field.message{height:76px;line-height:20px;padding-top:10px}
.btn-send{display:block;width:148px;height:42px;line-height:42px;background:var(--black);color:var(--white);font-size:15px;text-align:center;margin-top:14px;letter-spacing:.5px}
.contact-info{position:absolute;left:657px;top:166px}
.contact-info h3{font-family:"Roboto",Arial,sans-serif;font-weight:400;font-size:23px;margin-bottom:18px}
.info-line{display:flex;align-items:center;gap:14px;font-size:15px;height:42px}
.info-line svg{flex:none}
.social{display:flex;gap:8px;margin-top:12px}
.social span{width:36px;height:36px;border-radius:50%;border:2px solid var(--white)}

/* Footer */
.site-footer{height:67px;background:var(--black);color:var(--white);font-size:12px;text-align:center;line-height:67px}
</style>
</head>
<body>

<section class="hero">
  <div class="hero-photo" role="img" aria-label="Photo of a driver in a truck cab checking a phone"></div>
  <div class="hero-shade"></div>
  <header class="site-header">
    <div class="brand"><span class="brand-dot"></span><span class="brand-name">KORVEL</span></div>
    <nav class="main-nav">
      <a class="active" href="#">HOME</a>
      <a href="#">ABOUT</a>
      <a href="#">LANTERNS</a>
      <a href="#">IT CONSULTANCY</a>
      <a href="#">CONTACT</a>
    </nav>
  </header>
  <h1 class="hero-title"><span class="line1">IT EXPERTISE FOR YOUR</span><span class="line2">BUSINESS AT ANY STAGE</span></h1>
  <svg class="hero-cut" width="1200" height="140" viewBox="0 0 1200 140" aria-hidden="true">
    <polygon points="0,0 600,122 1200,0 1200,140 0,140" fill="#e3e3e3"/>
  </svg>
  <div class="slider-dots"><span class="current"></span><span></span><span></span><span></span></div>
</section>

<section class="about">
  <h2 class="section-title">ABOUT US</h2>
  <div class="divider"><i></i><b></b><i></i></div>
  <p class="lead">Mauris vel lacus vitae felis vestibulum volutpat Etiam est nunc venenatis in tristique eu imperdiet ac nisl Cum sociis natoque penatibus et magnis dis parturient</p>
  <p class="body">Vivamus porttitor purus nisi eleifend libero a tempus libero lectus feugiat felis Morbi diam mauris viverra in gravida eu mattis in ante Morbi eget arcu Morbi porta libero id ullamcorper nonummy nibh ligula pulvinar metus eget consectetuer augue nisi quis lacus Ut ac mi quis lacus mollis aliquam Curabitur iaculis tempus eros Curabitur vel</p>
  <a class="btn-outline" href="#">READ MORE</a>
</section>

<section class="lanterns">
  <h2 class="section-title">KORVEL LANTERNS</h2>
  <div class="divider"><i></i><b></b><i></i></div>
  <p>Korvel lanterns has developed two cutting edge products using machine learning and deep learning.</p>
</section>

<section class="product-row">
  <div class="product-copy blue">
    <h3>ORIN</h3>
    <p>The primary cause of accidents on the road are caused by human error. Of these driver distraction and fatigue are the real problem. ORIN is a system for HGV/HMT drivers to make every journey safer - safer for the driver and safer to other road users. ORIN uses advanced deep learning techniques to monitor driver behavior in real time inside the cabin.</p>
    <a class="btn-light" href="#">READ MORE</a>
  </div>
  <div class="photo photo-office" role="img" aria-label="Photo of two colleagues discussing work at a desk with a computer"></div>
</section>

<section class="product-row row-wheel">
  <div class="photo photo-driver" role="img" aria-label="Photo of a smiling driver at the wheel of a truck"></div>
  <div class="product-copy dark">
    <h3>WheelWise</h3>
    <p>WheelWise is a machine learning system that tracks and analyzes live used car trading markets. It learns every aspect of a car ads, through which, it creates powerful market intelligence for all parties in the used car ecosystem:</p>
    <p>It gives inexperienced buyers independent market consensus price, depreciation and approximated running costs for cars</p>
    <a class="btn-light" href="#">READ MORE</a>
  </div>
</section>

<section class="consultancy">
  <div class="photo-meeting" role="img" aria-label="Photo of two businessmen working together on a laptop"></div>
  <div class="consultancy-copy">
    <h2>IT CONSULTANCY</h2>
    <p>Korvel Solutions is an IT consultancy firm with a difference We can provide IT expertise for your business at any stage - from initial idea to live systems.</p>
    <p>We have many years experience in machine learning, data mining, app development, DevOps and hardware design</p>
    <a class="btn-outline" href="#">READ MORE</a>
  </div>
</section>

<section class="contact">
  <h2 class="section-title">CONTACT US</h2>
  <div class="divider"><i></i><b></b><i></i></div>
  <form class="contact-form">
    <div class="field">Your Name</div>
    <div class="field">Email address</div>
    <div class="field">Phone number</div>
    <div class="field message">Message</div>
    <div class="btn-send">SEND</div>
  </form>
  <div class="contact-info">
    <h3>Korvel Solutions</h3>
    <div class="info-line">
      <svg width="34" height="34" viewBox="0 0 34 34" aria-hidden="true"><circle cx="17" cy="17" r="15.5" fill="none" stroke="#fff" stroke-width="2"/><path d="M17 9a5 5 0 0 0-5 5c0 4 5 10 5 10s5-6 5-10a5 5 0 0 0-5-5z" fill="none" stroke="#fff" stroke-width="1.8"/><circle cx="17" cy="14" r="1.8" fill="#fff"/></svg>
      <span>42 Harbor Lane, Suite 8, Austin TX 78701</span>
    </div>
    <div class="info-line">
      <svg width="34" height="34" viewBox="0 0 34 34" aria-hidden="true"><circle cx="17" cy="17" r="15.5" fill="none" stroke="#fff" stroke-width="2"/><path d="M12 10l3 0 1.5 4-2 1.5a9 9 0 0 0 4 4l1.5-2 4 1.5v3a2 2 0 0 1-2 2A13 13 0 0 1 10 12a2 2 0 0 1 2-2z" fill="none" stroke="#fff" stroke-width="1.6" stroke-linejoin="round"/></svg>
      <span>555.014.2290</span>
    </div>
    <div class="info-line">
      <svg width="34" height="34" viewBox="0 0 34 34" aria-hidden="true"><circle cx="17" cy="17" r="15.5" fill="none" stroke="#fff" stroke-width="2"/><rect x="10" y="12" width="14" height="10" fill="none" stroke="#fff" stroke-width="1.6"/><path d="M10 12l7 6 7-6" fill="none" stroke="#fff" stroke-width="1.6"/></svg>
      <span>hello@korvel.example</span>
    </div>
    <div class="social" aria-label="Social links"><span></span><span></span><span></span><span></span></div>
  </div>
</section>

<footer class="site-footer">© 2018 Korvel Solutions &nbsp;All right reserved &nbsp;Terms of Use</footer>

</body>
</html>
```